Counseling Practice Business Card

I need a professional looking business card incorporating my new logo that was just completed. Card needs to incorporate my name and title, description of my specialty, my address, my phone number, my fax number, my email and my website URL. I need to be able to choose design on/with different paper colors and textures.
I do not have a lot of business card ideas so I am open to anything but I want bold,sharp, clear card without additional designs other than my logo (see attached file info). I am open to different color backgrounds or paper colors including black. I do not like traditional brackets around area codes in phone number or dashes between numbers in phone number. Am open to other ways of presenting including periods between numbers as appropriate. I do not know enough to know what I like yet but I want card to coordinate and work together with my logo. My practice emphasizes natural mental health interventions so any use of color (with background paper color or the blue and green in my logo) that elicits nature is nice. In addition to black, any natural brown or wood looking background might be desirable also. Most of the offerings so far look very similar and boring.

Target Market(s)

Potential therapy clients and other professionals

Contact Information for Business Card

Card information:
Gerald M. Whitcombe, Ph.D.
Licensed Clinical Psychologist
Integrative Health Coach
4812 Marlowe Ridge Blvd SE
Suite 310
Duluth, GA 30096
(770) 415-2983 phone
(770) 581-4096 fax
drgeraldwhitcombe@quillmarsh.net
brightfernwellness.net

Font styles to use
Serif
Sans Serif
Other font styles liked:
• anything that you think looks crisp, clear and easily readable

Requirements
Must have
• Any color used should coordinate with my logo design (see attached files).
• Card should be printed horizontally so top and bottom are longest sides of rectangle.
• Background color or paper color should complement and highlight logo. Do not like a white background. black, grey, brown or any color my logo would blend well with.
Nice to have
• I would like designer to utilize color to highlight letters/name or phone-fax-web symbols.
• Bottom edge of card could be highlighted if appropriate to an idea.
Should not have
• I would NOT want the card to have a pure white background at all.
• No clear cards.
• Cards should be oriented with long sides on bottom and top, NOT sides. DO NOT LIKE THIS THIN TALL ORIENTATION.

```html
<!DOCTYPE html>
<html lang="en">
<head>
<meta charset="utf-8">
<title>Brightfern Wellness – Business Card</title>
<link href="https://fonts.googleapis.com/css2?family=Oswald:wght@600&family=Roboto:wght@400;500&display=swap" rel="stylesheet">
<style>
  :root {
    --backdrop: #3b3b3d;
    --card: #232325;
    --card-front: #1c1c1e;
    --emboss: #5e5e62;
    --blue: #2f7fcf;
    --green: #1f7a3a;
    --white: #f4f4f4;
  }
  * { margin: 0; padding: 0; box-sizing: border-box; }
  html, body { width: 799px; height: 1200px; overflow: hidden; }
  body {
    background: var(--backdrop);
    font-family: "Roboto", sans-serif;
    position: relative;
  }
  .card {
    position: absolute;
    left: 80px;
    width: 640px;
    height: 366px;
    border-radius: 3px;
    overflow: hidden;
    box-shadow: 0 18px 40px rgba(0,0,0,.45);
  }
  .card--front { top: 120px; background: var(--card-front); }
  .card--back { top: 714px; background: var(--card); }

  .brand { display: flex; align-items: center; gap: 14px; }
  .brand__dot { width: 26px; height: 26px; border-radius: 50%; }
  .brand__name { font-weight: 500; letter-spacing: .5px; }

  .card--front .brand {
    position: absolute; inset: 0; justify-content: center;
  }
  .card--front .brand__dot { background: var(--emboss); width: 34px; height: 34px; }
  .card--front .brand__name { color: var(--emboss); font-size: 46px; }

  .card__waves { position: absolute; inset: 0; }

  .card--back .brand { position: absolute; left: 36px; top: 112px; }
  .card--back .brand__dot { background: var(--blue); }
  .card--back .brand__name { color: var(--blue); font-size: 31px; }

  .holder {
    position: absolute; right: 22px; top: 44px; text-align: right; color: var(--white);
  }
  .holder__name { font-family: "Oswald", sans-serif; font-weight: 600; font-size: 20px; letter-spacing: .3px; }
  .holder__title { font-size: 13px; line-height: 1.35; }

  .contacts {
    position: absolute; left: 38px; top: 186px; list-style: none; color: var(--white); font-size: 14px;
  }
  .contacts li { display: flex; align-items: center; gap: 10px; height: 22px; }
  .contacts svg { width: 13px; height: 13px; fill: var(--blue); flex: none; }

  .address {
    position: absolute; right: 34px; bottom: 34px; color: var(--white); font-size: 14px; line-height: 1.45;
  }
</style>
</head>
<body>

<section class="card card--front">
  <div class="brand">
    <span class="brand__dot"></span>
    <span class="brand__name">Brightfern Wellness</span>
  </div>
</section>

<section class="card card--back">
  <svg class="card__waves" viewBox="0 0 640 366" aria-hidden="true">
    <path d="M150 0 L640 0 L640 262 C560 250 480 170 410 122 C330 66 250 22 150 0 Z" fill="var(--blue)"/>
    <path d="M175 0 C270 12 350 50 420 96" fill="none" stroke="var(--green)" stroke-width="7"/>
    <path d="M122 14 C250 36 340 92 412 142 C482 190 560 262 640 280" fill="none" stroke="var(--green)" stroke-width="11"/>
  </svg>

  <div class="brand">
    <span class="brand__dot"></span>
    <span class="brand__name">Brightfern Wellness</span>
  </div>

  <div class="holder">
    <p class="holder__name">Gerald M. Whitcombe, Ph.D.</p>
    <p class="holder__title">Licensed Clinical Psychologist</p>
    <p class="holder__title">Integrative Health Coach</p>
  </div>

  <ul class="contacts">
    <li><svg viewBox="0 0 16 16"><path d="M3 1h3l1.5 4-2 1.2a9 9 0 0 0 4.3 4.3L11 8.5l4 1.5v3a2 2 0 0 1-2 2A12 12 0 0 1 1 3a2 2 0 0 1 2-2z"/></svg>770.415.2983</li>
    <li><svg viewBox="0 0 16 16"><path d="M4 1h7v4H4zM1 6h14v7h-3v2H4v-2H1zm4 5v3h6v-3z"/></svg>770.581.4096</li>
    <li><svg viewBox="0 0 16 16"><path d="M1 3h14v10H1zm1.5 1.2V5l5.5 4 5.5-4v-.8z"/></svg>brightfernwellness.net</li>
    <li><svg viewBox="0 0 16 16"><circle cx="8" cy="8" r="7"/></svg>drgeraldwhitcombe@quillmarsh.net</li>
  </ul>

  <address class="address" style="font-style:normal">
    4812 Marlowe Ridge Blvd SE<br>
    Suite 310 Duluth, GA 30096
  </address>
</section>

</body>
</html>
```